Existing Website Requiring new Pages

I have an existing word press website that was built using elementor.
Website: www.tallowcrestcare.com.au
I require the Vacancies page (https://www.tallowcrestcare.com.au/vacancies/) to be modified to display our new properties along with minor tweaks to how the information is presented.
The vacancies to be displayed are the exactly the same as those that are located on the homepage of QMR website (https://qmr.org.au/)
The new pages that link off the Vacancies tab will require custom design.
There are roughly 8 pages/properties to be incorporated. i wish for the design to be very similar to that displayed in the following link; https://www.polunda.com.au/vacancies/merrylands
Along with this the back end has not been updated for the last 3 years so it also requires some maintenance.
Website is in the disability industry and the custom pages will display information relative to Property Vacancies.
I have attached a ZIP file with some design guides, the information for each of the properties (which will need to be modified to show our business name Tallowcrest Care) and the example of how it is to look based off the Polunda website.
If you guys have any suggestions or ideas on how to make this more presentable or possible i'm open to your ideas.
Target Market(s)
People looking for SDA properties custom built for people with a disability
Industry/Entity Type
Disability
Coding
Coded - Design and coding required
Number of Pages Required
5+ page

```html
<!DOCTYPE html>
<html lang="en">
<head>
<meta charset="utf-8">
<title>Specialist Disability Accommodation in Guildford – Tallowcrest Care</title>
<link rel="stylesheet" href="https://fonts.googleapis.com/css2?family=Roboto:wght@400;500;700;900&display=swap">
<style>
:root{
  --orange:#fa8c55;
  --orange-soft:#fdd9c2;
  --cream:#fdf5e8;
  --beige:#f6ebda;
  --ink:#1f1f1f;
  --body:#3d3d3d;
  --muted:#8a8a8a;
  --line:#e6e0d6;
  --dark:#2b2b2b;
  --white:#fff;
  --teal:#34b3c4;
  --purple:#7c5cc9;
  --green:#2fbf71;
  --blue:#2f9be0;
}
*{box-sizing:border-box;margin:0;padding:0}
html,body{width:1200px;height:4129px;overflow:hidden;background:var(--white);font-family:'Roboto',Arial,sans-serif;color:var(--ink)}
.page{position:relative;width:1200px;height:4129px}
.abs{position:absolute}

/* header */
.site-header{position:absolute;left:0;top:0;width:1200px;height:106px;background:var(--white)}
.brand{position:absolute;left:137px;top:30px;display:flex;align-items:center;gap:10px;font-weight:700;font-size:22px;color:var(--ink)}
.brand .dot{width:30px;height:30px;border-radius:50%;background:var(--orange)}
.nav{position:absolute;right:134px;top:46px;display:flex;gap:22px;font-size:10.5px;font-weight:700;letter-spacing:.8px}
.nav a{color:#333;text-decoration:none}
.nav a.active{color:var(--orange)}

/* hero */
.ph{position:absolute;background:linear-gradient(180deg,#9fc7ea 0%,#c9b79a 55%,#6f9a4a 100%)}

/* listing intro */
.back{left:137px;top:622px;font-size:11px;color:#333}
.tag{left:253px;top:612px;width:110px;height:32px;background:var(--beige);font-size:11px;display:flex;align-items:center;justify-content:center;color:#333}
.title{left:137px;top:654px;width:400px;font-size:38px;font-weight:700;line-height:43px;color:var(--ink)}
.intro{left:137px;top:796px;width:370px;font-size:11.5px;line-height:20px;color:var(--body)}
.btn{position:absolute;display:flex;align-items:center;justify-content:center;font-size:12.5px;font-weight:500;text-decoration:none}
.btn-orange{background:var(--orange);color:var(--white)}
.btn-beige{background:var(--beige);color:var(--ink)}

/* enquiry */
.enquiry{left:568px;top:608px;width:498px;height:370px;background:var(--cream)}
.enquiry h2{position:absolute;left:0;right:0;top:40px;text-align:center;font-size:28px;font-weight:900;color:var(--ink)}
.enquiry .phone{position:absolute;left:0;right:0;top:80px;text-align:center;font-size:16px;font-weight:700;display:flex;justify-content:center;align-items:center;gap:5px}
.field{position:absolute;width:206px;height:36px;background:var(--white);border:1px solid var(--line);font-size:10px;color:var(--muted);padding:0 15px;display:flex;align-items:center;justify-content:space-between}
.enquiry .submit{position:absolute;left:38px;top:287px;width:426px;height:50px;background:var(--orange);color:var(--white);font-size:17px;font-weight:700;display:flex;align-items:center;justify-content:center}

/* features */
.h-section{font-size:24px;font-weight:500;color:var(--ink)}
.feature{position:absolute;display:flex;align-items:center;gap:18px;font-size:13px;color:#333}
.feature .ico{width:90px;height:90px;border-radius:50%;background:var(--cream);display:flex;align-items:center;justify-content:center;flex:none}
.feature .ico span{width:46px;height:46px;border-radius:10px;background:linear-gradient(135deg,#f4b17f,#5fa9d6)}

.gallery-btn{left:442px;top:1527px;width:319px;height:63px;background:var(--orange);color:var(--white);font-size:26px;font-weight:700;display:flex;align-items:center;justify-content:center;letter-spacing:.5px}

.center-h{position:absolute;left:0;width:1200px;text-align:center;font-weight:500;color:var(--ink)}

.map{left:137px;top:2302px;width:929px;height:428px;background:linear-gradient(135deg,#e6ddc9,#d9ccb0 60%,#cfc2a6)}

/* contact band */
.band{left:0;top:2813px;width:1200px;height:246px;background:var(--orange)}
.band-item{position:absolute;top:45px;width:300px;text-align:center;color:var(--white)}
.band-item .circ{width:100px;height:100px;border-radius:50%;background:var(--orange-soft);margin:0 auto;display:flex;align-items:center;justify-content:center}
.band-item h3{margin-top:26px;font-size:20px;font-weight:700}
.band-item p{margin-top:14px;font-size:12px}

/* cards */
.card{position:absolute;top:3204px;width:300px;height:384px;background:#f7f5f2}
.card .img{position:absolute;left:0;top:0;width:300px;height:250px;background:linear-gradient(180deg,#a9cdef 0%,#c8a98b 55%,#5f8d43 100%)}
.badge{position:absolute;top:14px;height:14px;font-size:7.5px;font-weight:700;color:var(--white);display:flex;align-items:center;padding:0 5px}
.card h4{position:absolute;left:23px;top:266px;font-size:17px;font-weight:700}
.card .type{position:absolute;left:23px;top:294px;font-size:10px;color:#444}
.card .desc{position:absolute;left:23px;top:313px;font-size:10px;color:#333}
.card .details{position:absolute;left:23px;top:335px;width:94px;height:33px;background:var(--orange);color:var(--white);font-size:11px;font-weight:700;display:flex;align-items:center;justify-content:center}

.pill{position:absolute;top:3657px;height:66px;border-radius:33px;font-size:15px;font-weight:700;display:flex;align-items:center;justify-content:center}

/* footer */
.footer{left:0;top:3803px;width:1200px;height:264px;background:var(--white);box-shadow:0 -6px 12px rgba(0,0,0,.04)}
.f-contact{position:absolute;left:150px;font-size:11px;color:var(--muted);display:flex;align-items:center;gap:7px}
.f-contact i{width:10px;height:10px;border:1.5px solid var(--orange);border-radius:2px;display:inline-block}
.social{position:absolute;left:528px;width:30px;height:30px;border-radius:50%;background:#1f2f55}
.social.first{background:#6a3fa0}
.f-col{position:absolute;top:3846px;width:212px}
.f-col h5{font-size:12px;font-weight:500;letter-spacing:.8px;color:#222;border-left:2px solid var(--blue);padding-left:12px}
.f-col ul{list-style:none;margin-top:16px}
.f-col li{font-size:11px;line-height:20px;color:var(--muted);border-bottom:1px solid #eee;padding:4px 0}
.bottom{left:0;top:4067px;width:1200px;height:62px;background:var(--dark);color:#bbb;font-size:9px;display:flex;align-items:center;justify-content:center}
</style>
</head>
<body>
<div class="page">

<header class="site-header">
  <div class="brand"><span class="dot"></span>Tallowcrest Care</div>
  <nav class="nav">
    <a href="#">HOME</a><a href="#">ABOUT US</a><a href="#" class="active">WHAT WE DO ▾</a><a href="#">REFERRALS</a><a href="#">FEEDBACK</a><a href="#">CONTACT US</a>
  </nav>
</header>

<section aria-label="Property photos">
  <div class="ph" style="left:0;top:106px;width:293px;height:219px" role="img" aria-label="Single storey brick home with garage and lawn"></div>
  <div class="ph" style="left:0;top:331px;width:293px;height:221px" role="img" aria-label="Heritage cottage facade"></div>
  <div class="ph" style="left:301px;top:106px;width:600px;height:446px;background:linear-gradient(180deg,#9cc6ec 0%,#b66a4f 45%,#cf8466 75%,#4f8a3a 100%)" role="img" aria-label="Brick home with paved driveway and hedges"></div>
  <div class="ph" style="left:908px;top:106px;width:292px;height:219px" role="img" aria-label="Brick home behind landscaped garden"></div>
  <div class="ph" style="left:908px;top:331px;width:292px;height:221px" role="img" aria-label="Modern home with grey garage door"></div>
</section>

<a class="abs back">‹ &nbsp;Back to Listings</a>
<div class="abs tag">Available Now</div>
<h1 class="abs title">Specialist Disability Accommodation SDA in Guildford</h1>
<p class="abs intro">Lorem Ipsum is simply dummy text of the printing and typesetting industry. Lorem Ipsum has been the industry's standard dummy text ever since the 1500s, when an unknown printer took a galley of type and scrambled it to make a type specimen book. It has survived not</p>
<a class="btn btn-orange" style="left:137px;top:905px;width:115px;height:43px">Enquire Now</a>
<a class="btn btn-beige" style="left:264px;top:905px;width:205px;height:43px">Download Property Brochure</a>

<form class="abs enquiry">
  <h2>ENQUIRE NOW</h2>
  <div class="phone"><svg width="13" height="13" viewBox="0 0 24 24"><path fill="#fa8c55" d="M6.6 10.8a15 15 0 006.6 6.6l2.2-2.2c.3-.3.7-.4 1-.2 1.1.4 2.3.6 3.6.6.6 0 1 .4 1 1V20c0 .6-.4 1-1 1A17 17 0 013 4c0-.6.4-1 1-1h3.5c.6 0 1 .4 1 1 0 1.3.2 2.5.6 3.6.1.3 0 .7-.2 1z"/></svg>1300 555 014</div>
  <div class="field" style="left:38px;top:134px">Enter your name</div>
  <div class="field" style="left:258px;top:134px">Enter your Address</div>
  <div class="field" style="left:38px;top:184px">Role<span>▾</span></div>
  <div class="field" style="left:258px;top:184px">State<span>▾</span></div>
  <div class="field" style="left:38px;top:233px">Postcode</div>
  <div class="field" style="left:258px;top:233px">Phone</div>
  <div class="submit">ENQUIRE NOW</div>
</form>

<h2 class="abs h-section" style="left:137px;top:996px">Property Features</h2>
<div class="feature" style="left:137px;top:1063px"><div class="ico" role="img" aria-label="Air conditioning icon"><span></span></div>Ducted air conditioning</div>
<div class="feature" style="left:428px;top:1063px"><div class="ico" role="img" aria-label="Walkway icon"><span></span></div>Disability access walkways</div>
<div class="feature" style="left:741px;top:1063px"><div class="ico" role="img" aria-label="Intercom icon"><span></span></div>24/7 Intercom</div>
<div class="feature" style="left:137px;top:1181px"><div class="ico" role="img" aria-label="Wash basin icon"><span></span></div>Accessible wash basins</div>
<div class="feature" style="left:428px;top:1181px"><div class="ico" role="img" aria-label="Ceiling hoist icon"><span></span></div>Ceiling hoist</div>
<div class="feature" style="left:741px;top:1181px"><div class="ico" role="img" aria-label="Wifi router icon"><span></span></div>Wifi internet</div>

<h2 class="abs h-section" style="left:137px;top:1311px">Comes with the lifestyle</h2>
<div class="feature" style="left:137px;top:1377px"><div class="ico" role="img" aria-label="Wash basin icon"><span></span></div>Accessible wash basins</div>
<div class="feature" style="left:430px;top:1377px"><div class="ico" role="img" aria-label="Barbecue icon"><span></span></div>Communal Rooftop BBQ</div>

<div class="abs gallery-btn">PROPERTY GALLERY</div>

<section aria-label="Property gallery">
  <div class="ph" style="left:137px;top:1650px;width:303px;height:254px" role="img" aria-label="Cottage with red roof and verandah"></div>
  <div class="ph" style="left:450px;top:1650px;width:303px;height:254px;background:linear-gradient(180deg,#4fa3e6,#d7d6d0 60%,#6f9a4a)" role="img" aria-label="Apartment buildings with garden path"></div>
  <div class="ph" style="left:762px;top:1650px;width:304px;height:254px;background:linear-gradient(180deg,#2c5aa8,#d9c7a0 60%,#2f74c9)" role="img" aria-label="Modern house with pool at dusk"></div>
  <div class="ph" style="left:137px;top:1914px;width:303px;height:255px;background:linear-gradient(180deg,#5aa9e8,#dedcd6 55%,#5f8a45)" role="img" aria-label="Apartment blocks along a walkway"></div>
  <div class="ph" style="left:450px;top:1914px;width:303px;height:255px;background:linear-gradient(180deg,#3e8fe0,#e4cfa8 55%,#8a6a4a)" role="img" aria-label="High-rise residential towers"></div>
  <div class="ph" style="left:762px;top:1914px;width:304px;height:255px;background:linear-gradient(180deg,#6b7bb0,#6a6d74 50%,#b9bbbe)" role="img" aria-label="Grey two storey modern home"></div>
</section>

<h2 class="center-h" style="top:2222px;font-size:32px">Mount Druitt NSW 2161</h2>
<div class="abs map" role="img" aria-label="Map of western Sydney showing the property location in Mount Druitt"></div>
<svg class="abs" style="left:758px;top:2400px" width="80" height="100" viewBox="0 0 80 100" aria-hidden="true"><path d="M40 4a34 34 0 00-34 34c0 24 34 58 34 58s34-34 34-58A34 34 0 0040 4z" fill="#b93f4a"/><circle cx="40" cy="38" r="24" fill="#fff"/><path d="M26 42l14-12 14 12v10H26z" fill="#b93f4a"/></svg>

<section class="abs band">
  <div class="band-item" style="left:140px"><div class="circ"><svg width="60" height="40" viewBox="0 0 60 40"><rect x="2" y="2" width="56" height="36" rx="3" fill="none" stroke="#fa8c55" stroke-width="3"/><path d="M2 4l28 20 28-20" fill="none" stroke="#fa8c55" stroke-width="3"/></svg></div><h3>MESSAGE US</h3><p>info@tallowcrestcare.com.au</p></div>
  <div class="band-item" style="left:457px"><div class="circ"><svg width="50" height="50" viewBox="0 0 24 24"><path fill="#fa8c55" d="M6.6 10.8a15 15 0 006.6 6.6l2.2-2.2c.3-.3.7-.4 1-.2 1.1.4 2.3.6 3.6.6.6 0 1 .4 1 1V20c0 .6-.4 1-1 1A17 17 0 013 4c0-.6.4-1 1-1h3.5c.6 0 1 .4 1 1 0 1.3.2 2.5.6 3.6.1.3 0 .7-.2 1z"/></svg></div><h3>CALL US</h3><p>1300 555 014</p></div>
  <div class="band-item" style="left:767px"><div class="circ"><svg width="52" height="40" viewBox="0 0 52 40"><rect x="3" y="6" width="46" height="28" rx="4" fill="none" stroke="#fa8c55" stroke-width="3"/><path d="M14 20h24" stroke="#fa8c55" stroke-width="3"/></svg></div><h3>FOLLOW US</h3><p>@tallowcrestcare</p></div>
</section>

<h2 class="center-h" style="top:3112px;font-size:36px">Browse More Properties</h2>

<article class="card" style="left:137px">
  <div class="img" role="img" aria-label="Penrith home with grey garage"></div>
  <span class="badge" style="left:12px;background:var(--purple)">FEATURED</span>
  <span class="badge" style="left:124px;background:var(--green)">AVAILABLE NOW</span>
  <span class="badge" style="left:205px;background:var(--blue)">CURRENT VACANCY</span>
  <h4>Penrith</h4><div class="type">4 Bedroom SIL Home</div><div class="desc">Lorem Ipsum is simply dummy text of the printing</div><div class="details">DETAILS</div>
</article>
<article class="card" style="left:451px">
  <div class="img" style="background:linear-gradient(180deg,#9cc6ec,#b66a4f 45%,#cf8466 75%,#4f8a3a)" role="img" aria-label="Mount Druitt brick home with paved driveway"></div>
  <span class="badge" style="left:12px;background:var(--purple)">FEATURED</span>
  <span class="badge" style="left:124px;background:var(--green)">AVAILABLE NOW</span>
  <span class="badge" style="left:205px;background:var(--blue)">CURRENT VACANCY</span>
  <h4>Mount Druitt</h4><div class="type">4 Bedroom SIL Home</div><div class="desc">Lorem Ipsum is simply dummy text of the printing</div><div class="details">DETAILS</div>
</article>
<article class="card" style="left:765px">
  <div class="img" style="background:linear-gradient(180deg,#3f88dc,#e3d3b2 55%,#6b9a45)" role="img" aria-label="Casula home with lawn"></div>
  <span class="badge" style="left:12px;background:var(--purple)">FEATURED</span>
  <span class="badge" style="left:124px;background:var(--green)">AVAILABLE NOW</span>
  <span class="badge" style="left:205px;background:var(--blue)">CURRENT VACANCY</span>
  <h4>Casula</h4><div class="type">4 Bedroom SIL Home</div><div class="desc">Lorem Ipsum is simply dummy text of the printing</div><div class="details">DETAILS</div>
</article>

<a class="pill" style="left:375px;width:231px;background:var(--orange);color:var(--white)">VIEW ALL VACANCIES</a>
<a class="pill" style="left:620px;width:225px;background:var(--beige);color:var(--ink)">CONTACT US</a>

<footer class="abs footer"></footer>
<div class="brand" style="top:3895px;left:152px;font-size:20px"><span class="dot"></span>Tallowcrest Care</div>
<div class="f-contact" style="top:3987px"><i></i>Email: info@tallowcrestcare.com.au</div>
<div class="f-contact" style="top:4006px"><i></i>Phone: +61 0400 555 827</div>
<div class="f-contact" style="top:4026px"><i></i>Operating Hours: 9AM To 5PM Monday - Friday</div>
<span class="social first" style="top:3863px"></span>
<span class="social" style="top:3899px"></span>
<span class="social" style="top:3935px;background:#111"></span>
<span class="social" style="top:3972px;background:#1f6fb5"></span>
<div class="f-col" style="left:613px"><h5>ACCOMMODATION</h5><ul><li>Supported Independent Living (SIL)</li><li>Specialist Disability Accommodation (SDA)</li><li>Short term Accommodation (Respite)</li><li>Vacancies</li></ul></div>
<div class="f-col" style="left:846px"><h5>WHAT WE DO</h5><ul><li>In Home Care</li><li>Social &amp; Community Services</li><li>Therapeutic Supports</li><li>Support Coordination</li><li>Home Modifications</li></ul></div>
<div class="abs bottom">© Copyright 2021 | Tallowcrest Care | All Rights Reserved.</div>

</div>
</body>
</html>
```